Silas Merton Moving DL Flyer

We need a double sided DL flyer to give to patients to let them know that we are moving location.
On one side we would like it to read:
"We Are Moving!" and "November 2017" and our logo.
On the other side we would like it to read:
"Same Great Staff"
"Same Great Service"
"Bigger, Brighter and Better"
"New Location at 59 Quarry Ln"
with a map below (attached)
The flyer should follow our practice branding. Attached is a copy of our business card as an example of this.

```html
<!DOCTYPE html>
<html lang="en">
<head>
<meta charset="utf-8">
<title>Silas Merton Optometry – Moving DL Flyer</title>
<link href="https://fonts.googleapis.com/css2?family=Oswald:wght@500&family=Roboto+Condensed:wght@400;700&family=Roboto:wght@400&display=swap" rel="stylesheet">
<style>
  :root {
    --backdrop: #2a2a2a;
    --paper: #ffffff;
    --plum: #4a3552;
    --plum-deep: #3d2b45;
    --band-start: #5a3c68;
    --band-mid: #9670a6;
    --band-end: #5a3c68;
    --ink: #2b2b2b;
    --muted: #555555;
    --map-grey: #c8c8c8;
    --photo-light: #dfe6ec;
    --photo-mid: #8fa8c2;
  }
  * { box-sizing: border-box; margin: 0; padding: 0; }
  html, body { width: 1200px; height: 1020px; overflow: hidden; }
  body { background: var(--backdrop); position: relative; font-family: "Roboto Condensed", sans-serif; }

  .flyer {
    position: absolute; top: 136px; width: 374px; height: 749px;
    background: var(--paper); overflow: hidden;
  }
  .flyer--front { left: 200px; }
  .flyer--back { left: 626px; }

  .brand {
    position: absolute; top: 20px; left: 0; width: 100%;
    text-align: center; color: var(--ink);
  }
  .brand__name {
    font-family: "Roboto", sans-serif; font-weight: 400; color: var(--ink);
    line-height: 1.05;
  }
  .brand__name .small { display: block; font-size: 17px; }
  .brand__name .large { display: block; font-size: 31px; }
  .brand__tagline {
    margin-top: 4px; font-family: "Roboto", sans-serif; font-size: 12px; color: var(--plum);
  }

  .hero-photo {
    position: absolute; top: 126px; left: 0; width: 100%; height: 344px;
    background: radial-gradient(ellipse at 50% 55%, var(--photo-mid) 0%, #a9bccf 45%, var(--photo-light) 100%);
  }

  .headline-intro {
    position: absolute; top: 496px; left: 0; width: 100%; text-align: center;
    font-family: "Roboto Condensed", sans-serif; font-weight: 400; font-size: 40px;
    color: var(--plum); letter-spacing: 1px;
  }
  .headline-rule {
    position: absolute; top: 547px; left: 80px; width: 214px; height: 1px; background: #999;
  }
  .headline-main {
    position: absolute; top: 532px; left: 0; width: 100%; text-align: center;
    font-family: "Oswald", sans-serif; font-weight: 500; font-size: 92px; line-height: 1.1;
    color: var(--plum); letter-spacing: 1px;
  }
  .headline-date {
    position: absolute; top: 640px; left: 0; width: 100%; text-align: center;
    font-weight: 700; font-size: 27px; color: var(--ink);
  }

  .band {
    position: absolute; left: 0; width: 100%;
    background: linear-gradient(90deg, var(--band-start), var(--band-mid) 50%, var(--band-end));
    color: #fff; text-align: center; font-weight: 700;
    display: flex; align-items: center; justify-content: center;
  }
  .band--web { top: 690px; height: 36px; font-family: "Roboto", sans-serif; font-size: 17px; font-weight: 400; }
  .band--promise { top: 589px; height: 65px; font-size: 27px; }

  .location-map {
    position: absolute; top: 120px; left: 0; width: 100%; height: 370px;
    background: linear-gradient(160deg, #d2d2d2, var(--map-grey) 60%, #bdbdbd);
  }

  .staff-line {
    position: absolute; top: 502px; left: 0; width: 100%; text-align: center;
    font-weight: 700; font-size: 40px; color: var(--plum);
  }
  .service-line {
    position: absolute; top: 548px; left: 0; width: 100%; text-align: center;
    font-weight: 700; font-size: 24px; color: var(--plum);
  }

  .call {
    position: absolute; top: 670px; left: 14px; color: var(--plum-deep); font-weight: 700;
  }
  .call__label { font-size: 19px; line-height: 1; }
  .call__number { font-size: 39px; line-height: 1.05; }
  .contact-divider {
    position: absolute; top: 672px; left: 194px; width: 1px; height: 64px; background: #888;
  }
  .contact-list {
    position: absolute; top: 677px; left: 204px; list-style: none;
    font-family: "Roboto", sans-serif; font-size: 11.5px; color: var(--ink);
  }
  .contact-list li { display: flex; align-items: center; gap: 6px; height: 18px; }
  .contact-list svg { flex: none; }
</style>
</head>
<body>

<section class="flyer flyer--front">
  <header class="brand">
    <div class="brand__name"><span class="small">Silas Merton</span><span class="large">Optometry</span></div>
    <div class="brand__tagline">See Better. See Us.</div>
  </header>
  <div class="hero-photo" role="img" aria-label="Photo of a smiling couple in denim shirts making glasses shapes with their hands"></div>
  <div class="headline-intro">WE ARE</div>
  <div class="headline-rule"></div>
  <div class="headline-main">MOVING</div>
  <div class="headline-date">NOVEMBER 2017</div>
  <div class="band band--web">www.silasmerton.com.au</div>
</section>

<section class="flyer flyer--back">
  <header class="brand">
    <div class="brand__name"><span class="small">Silas Merton</span><span class="large">Optometry</span></div>
    <div class="brand__tagline">See Better. See Us.</div>
  </header>
  <div class="location-map" role="img" aria-label="Street map showing the new practice location beside the marketplace, car parking and neighbouring shops"></div>
  <div class="staff-line">Same Great Staff</div>
  <div class="service-line">Same Great Service</div>
  <div class="band band--promise">BIGGER, BRIGHTER AND BETTER</div>
  <div class="call">
    <div class="call__label">CALL NOW</div>
    <div class="call__number">6541 7720</div>
  </div>
  <div class="contact-divider"></div>
  <ul class="contact-list">
    <li><svg width="10" height="10" viewBox="0 0 10 10"><circle cx="5" cy="5" r="4.3" fill="none" stroke="#555" stroke-width="1"/><circle cx="5" cy="5" r="2" fill="#555"/></svg>New Location at 59 Quarry Ln</li>
    <li><svg width="10" height="10" viewBox="0 0 10 10"><circle cx="5" cy="5" r="4.3" fill="none" stroke="#555" stroke-width="1"/><circle cx="5" cy="5" r="2" fill="#555"/></svg>silas@silasmerton.com.au</li>
    <li><svg width="10" height="10" viewBox="0 0 10 10"><circle cx="5" cy="5" r="4.3" fill="none" stroke="#555" stroke-width="1"/><circle cx="5" cy="5" r="2" fill="#555"/></svg>www.silasmerton.com.au</li>
  </ul>
</section>

</body>
</html>
```